Marrowby Water Taxi and Transport Business Card

I need business cards for my new water taxi and freight transport business I have started here in Kodiak Alaska. Kodiak is a remote island in the middle of the gulf of Alaska. There are seven native villages around the island and Kodiak is the #2 fishing port in the United States. We also have the largest Coast Guard Base in the U.S. My company will be providing water taxi and freight transport logistics to the villages and many hunting and fishing lodges as well as remote properties around the island.

I would like a business card that isn't status quo, something that stands out, either in feel or appearance. I do like clean minimal designs but it needs to have the necessary contact info on it.

Target Market(s)

remote lodge / property owners, residents of the many villages around Kodiak and any one wanting to enjoy the great outdoors of Kodiak Alaska

Industry/Entity Type

Business

Contact Information for Business Card

I like clean simple designs that aren't cluttered but still provide the necessary information

Colors
0255a3
3277b5
33a4d5
9bcb3c
add136
fbed22
ffc214
f78f20
f37122

Requirements
Must have
• logo and contact info
• Captain Mason Elwick
• www.marrowbyferryline.com
• mason@marrowbyferryline.com

```html
<!DOCTYPE html>
<html lang="en">
<head>
<meta charset="utf-8">
<title>Marrowby Water Taxi and Transport Business Card</title>
<link href="https://fonts.googleapis.com/css2?family=Montserrat:wght@400;600;700&family=Open+Sans:wght@400;600&display=swap" rel="stylesheet">
<style>
  :root {
    --navy: #0255a3;
    --mid-blue: #3277b5;
    --sky: #33a4d5;
    --orange: #f78f20;
    --sun: #ffc214;
    --ink: #4a4f57;
    --paper: #ffffff;
    --backdrop: #e9ecef;
  }
  * { box-sizing: border-box; margin: 0; padding: 0; }
  html, body {
    width: 1200px; height: 950px; overflow: hidden;
    background: var(--backdrop);
  }
  .sheet {
    position: relative; width: 1200px; height: 950px;
  }
  .card {
    position: absolute; left: 250px; width: 700px; height: 400px;
    overflow: hidden; border-radius: 4px;
    box-shadow: 0 8px 24px rgba(0,0,0,.18);
    background: var(--paper);
  }
  .card--front { top: 50px; }
  .card--back { top: 500px; }

  /* Front */
  .front-photo {
    position: absolute; inset: 0;
    background:
      linear-gradient(180deg, #9fc9e8 0%, #4f8fc9 30%, #1d5fa6 48%, #2f7fc0 62%, #7fb4de 78%, #0c3f7a 100%);
  }
  .front-brand {
    position: absolute; left: 0; right: 0; top: 150px;
    text-align: center; color: var(--paper);
    font-family: "Montserrat", sans-serif;
  }
  .front-brand__name {
    font-weight: 700; font-size: 56px; letter-spacing: 3px; line-height: 1;
  }
  .front-brand__tagline {
    font-family: "Open Sans", sans-serif;
    font-size: 19px; letter-spacing: 1px; margin-top: 6px;
  }
  .front-social {
    position: absolute; right: 190px; top: 292px; display: flex; gap: 10px;
  }
  .front-social span {
    width: 24px; height: 24px; border-radius: 50%;
    border: 2px solid var(--paper); background: rgba(255,255,255,.25);
  }

  /* Back */
  .back-wave { position: absolute; inset: 0; }
  .back-person {
    position: absolute; right: 50px; top: 46px; text-align: right;
    color: var(--paper);
  }
  .back-person__name {
    font-family: "Montserrat", sans-serif; font-weight: 700;
    font-size: 26px; letter-spacing: 1px;
  }
  .back-person__role {
    font-family: "Open Sans", sans-serif; font-size: 17px; margin-top: 2px;
  }
  .back-divider {
    position: absolute; left: 405px; top: 190px; width: 1px; height: 180px;
    background: #d4d8dd;
  }
  .back-contact {
    position: absolute; left: 428px; top: 196px;
    font-family: "Open Sans", sans-serif; font-size: 15px; color: var(--ink);
    line-height: 24px; list-style: none;
  }
  .back-contact li { display: flex; align-items: center; gap: 8px; }
  .back-contact svg { width: 14px; height: 14px; fill: var(--navy); flex: none; }
  .back-contact .plain { padding-left: 0; }
  .back-brand {
    position: absolute; left: 80px; top: 262px; width: 270px; text-align: center;
    font-family: "Montserrat", sans-serif; color: var(--navy);
  }
  .back-brand__dot {
    width: 34px; height: 34px; border-radius: 50%; background: var(--orange);
    margin: 0 auto 8px;
  }
  .back-brand__name {
    font-weight: 700; font-size: 38px; letter-spacing: 2px; line-height: 1;
  }
  .back-brand__tagline {
    font-weight: 700; font-size: 15px; margin-top: 6px;
  }
</style>
</head>
<body>
<main class="sheet">

  <section class="card card--front">
    <div class="front-photo" role="img" aria-label="Photograph of a boat's wake on open water at dusk with mountains on the horizon"></div>
    <div class="front-brand">
      <div class="front-brand__name">MARROWBY</div>
      <div class="front-brand__tagline">Water Taxi &amp; Transport</div>
    </div>
    <div class="front-social" aria-label="Social profiles">
      <span></span><span></span><span></span>
    </div>
  </section>

  <section class="card card--back">
    <svg class="back-wave" viewBox="0 0 700 400" preserveAspectRatio="none" aria-hidden="true">
      <defs>
        <linearGradient id="bandGradient" x1="0" y1="0" x2="1" y2="0">
          <stop offset="0" stop-color="var(--navy)"/>
          <stop offset="0.6" stop-color="var(--mid-blue)"/>
          <stop offset="1" stop-color="var(--sky)"/>
        </linearGradient>
      </defs>
      <path d="M0,0 H700 V112 C600,118 470,128 360,170 C250,212 140,222 60,218 C30,216 10,212 0,208 Z" fill="url(#bandGradient)"/>
      <path d="M700,118 C600,126 480,138 370,180 C260,222 150,236 60,234 C35,233 15,232 0,230 V222 C15,224 35,226 60,226 C150,228 255,214 362,172 C470,130 600,120 700,114 Z" fill="var(--orange)"/>
    </svg>

    <div class="back-person">
      <div class="back-person__name">MASON ELWICK</div>
      <div class="back-person__role">Captain</div>
    </div>

    <div class="back-divider"></div>

    <ul class="back-contact">
      <li class="plain">412 Harbor Bend Road</li>
      <li class="plain">Marrowby, Alaska 99601</li>
      <li>
        <svg viewBox="0 0 24 24"><path d="M6.6 10.8a15.1 15.1 0 0 0 6.6 6.6l2.2-2.2a1 1 0 0 1 1-.25 11.4 11.4 0 0 0 3.6.57 1 1 0 0 1 1 1V20a1 1 0 0 1-1 1A17 17 0 0 1 3 4a1 1 0 0 1 1-1h3.5a1 1 0 0 1 1 1c0 1.25.2 2.45.57 3.6a1 1 0 0 1-.25 1z"/></svg>
        907 555 0143
      </li>
      <li>
        <svg viewBox="0 0 24 24"><path d="M2 5h20v14H2z M2 5l10 8 10-8" stroke="#fff" stroke-width="1.5"/></svg>
        mason@marrowbyferryline.com
      </li>
      <li>
        <svg viewBox="0 0 24 24"><circle cx="12" cy="12" r="10"/><path d="M2 12h20M12 2c3 3 3 17 0 20M12 2c-3 3-3 17 0 20" stroke="#fff" stroke-width="1.4" fill="none"/></svg>
        www.marrowbyferryline.com
      </li>
    </ul>

    <div class="back-brand">
      <div class="back-brand__dot"></div>
      <div class="back-brand__name">MARROWBY</div>
      <div class="back-brand__tagline">Water Taxi &amp; Transport</div>
    </div>
  </section>

</main>
</body>
</html>
```